Social Media App Needs PPT Template

We need a PowerPoint template for a new social media company based in the DC area called "Bold Ledger." We provide an interactive digital platform for executives to share actionable advice. We would like to see designs that use our orange logo color as an accent, but are mainly grey, white, and black. The final design should communicate clean, chic, modern, and professional.

Target Market(s)

Executives

Industry/Entity Type

Information Technology

Font styles to use
Sans Serif

Colors
f78f20
fbe7d2
ffffff
000000
e8e8e8
757575

Requirements
Must have
• My project must have title page and many options for the body of the ppt (graphs, tables, etc). It also needs to be easy to modify. I must have someone who is experienced in creating powerpoint templates.
Nice to have
• It would be nice to have a very modern and clean design that includes the logo on every page, but still leaves a lot of room for the content of the slide
Should not have
• My design project should not look to busy.

```html
<!DOCTYPE html>
<html lang="en">
<head>
<meta charset="utf-8">
<title>Transition Page</title>
<link rel="stylesheet" href="https://fonts.googleapis.com/css2?family=Lato:wght@100;300&display=swap">
<style>
  :root {
    --board-grey: #555555;
    --label-white: #ffffff;
    --slide-glow: #0e3f5e;
    --slide-mid: #0c3047;
    --slide-dusk: #0b2432;
    --slide-deep: #0a1b22;
    --band-black: #01060a;
    --band-edge: #0a2230;
    --accent-orange: #f58f1d;
    --placeholder-ink: #2b5a72;
    --title-white: #ffffff;
  }
  * { margin: 0; padding: 0; box-sizing: border-box; }
  html, body {
    width: 1200px;
    height: 960px;
    overflow: hidden;
    background: var(--board-grey);
    font-family: "Lato", sans-serif;
  }
  .board {
    position: relative;
    width: 1200px;
    height: 960px;
  }
  .page-label {
    position: absolute;
    top: 74px;
    left: 0;
    width: 1172px;
    text-align: center;
    font-weight: 300;
    font-size: 27px;
    color: var(--label-white);
  }
  .slide {
    position: absolute;
    left: 110px;
    top: 135px;
    width: 975px;
    height: 732px;
    overflow: hidden;
    background: radial-gradient(ellipse 760px 640px at 370px 165px,
      var(--slide-glow) 0%, var(--slide-mid) 40%, var(--slide-dusk) 72%, var(--slide-deep) 100%);
  }
  .image-area {
    position: absolute;
    inset: 0;
  }
  .image-hint {
    position: absolute;
    left: 0;
    width: 975px;
    top: 284px;
    text-align: center;
    font-weight: 100;
    font-size: 74px;
    line-height: 1;
    color: var(--placeholder-ink);
  }
  .title-band {
    position: absolute;
    left: 0;
    top: 578px;
    width: 975px;
    height: 114px;
  }
  .title-band svg { display: block; }
  .band-title {
    position: absolute;
    right: 83px;
    top: 19px;
    font-weight: 300;
    font-size: 59px;
    line-height: 1.3;
    color: var(--title-white);
    white-space: nowrap;
  }
</style>
</head>
<body>
  <main class="board">
    <p class="page-label">Page 2</p>
    <section class="slide">
      <div class="image-area" role="img" aria-label="Full-bleed slide photograph area"></div>
      <p class="image-hint">Image Goes Here</p>
      <div class="title-band">
        <svg width="975" height="114" viewBox="0 0 975 114" aria-hidden="true">
          <polygon class="band-edge" points="430,0 442,0 320,114 309,114" fill="var(--band-edge)"/>
          <polygon class="band-fill" points="442,0 975,0 975,114 320,114" fill="var(--band-black)"/>
          <polygon class="accent-stripe" points="398,0 430,0 309,114 277,114" fill="var(--accent-orange)"/>
        </svg>
        <h1 class="band-title">Transition Page</h1>
      </div>
    </section>
  </main>
</body>
</html>
```